Bring me business with this creative business card

Design my new business card. I am looking for something different with an impact. People will take a look at this card & they will 1- see how different & creative I am, 2-understand what I do 3- Call me to meet me!

I make videos with a message, testimonials. I am dynamic, fun, creative & human. My new website is in construction but in the meantime you can check this old one: brightpath.ca & another one Tidebloom.com & tidebloom facebook page.
I make videos. sometimes with a cameraman, sometimes with my phone. As an ex Public Relations agent, the message is the most important thing for me. I want to make my clients shine! When they start with me they often remind me of a lamb, when I finish coaching them they are powerful like LIONS! That's why I need a powerful business card!

Target Market(s)

Entrepreneurs, solo entrepreneurs, small & medium companies & start ups. People i will meet while networking. People that need videos on their website & social Networks to get attention, to be visible. men & women. From 35 to 49 years old.
I am an ex Public relations agent. I used to send clients in traditional medias, now with videos they have more chances to be seen on google the new media. I do videos of the president, his team, his loyal clients saying how great the company is & expert videos like series so people can be seen for example every 1 st of every month with a short 2 minute video. Also with my 20 years in marketing & communications I can coach & give tips to anybody who needs it.
Target: anybody who would like my old website brightpath.ca & I also have another website but it will be off line soon: tidebloom.com could give you ideas.

Industry/Entity Type

Communications

Contact Information for Business Card

I am in Montreal,So the business cards have to be the usual size like we have in Montreal: 9 cm x 5 cm
Details:My text: Mathilde Tessier Communication coach/Chief Lion. "Creating Videos as unique as you" off: 514-555-0147 cell: 514-555-0183. tidebloom.com
mathilde@tidebloom.com logo facebook, youtube, instagram

Colors
f37122

Requirements
Must have
• Dynamic, happy. Orange. Be creative in the look but NOT the shape of the card. Easy to read. Big enough to read.
Should not have
• No funny shapes: no round, no square, just the usual. I love creative but NOT on shape.

```html
<!DOCTYPE html>
<html lang="en">
<head>
<meta charset="utf-8">
<title>Tidebloom — Business Card</title>
<link href="https://fonts.googleapis.com/css2?family=Roboto:wght@400;500&family=Roboto+Condensed:wght@400;500&display=swap" rel="stylesheet">
<style>
  :root {
    --brand-orange: #f37122;
    --deep-orange: #e8591f;
    --gold: #f5b323;
    --soft-peach: #fbe3cc;
    --soft-blush: #f8d6c8;
    --paper: #fbfbfa;
    --ink: #4a4a4a;
    --white: #ffffff;
    --stage: #e9e6e1;
  }
  * { box-sizing: border-box; margin: 0; padding: 0; }
  html, body { width: 1200px; height: 911px; overflow: hidden; }
  body { background: var(--stage); position: relative; font-family: "Roboto", sans-serif; }

  .card {
    position: absolute;
    width: 540px; height: 300px;
    border-radius: 3px;
    box-shadow: 0 10px 28px rgba(0,0,0,.16);
    overflow: hidden;
  }
  .card--front { left: 50px; top: 130px; background: var(--paper); }
  .card--back { left: 610px; top: 480px; background: var(--deep-orange); }

  /* front */
  .front__wash {
    position: absolute; right: 0; top: 0; width: 320px; height: 300px;
    background: linear-gradient(100deg, rgba(251,251,250,0) 0%, var(--soft-peach) 35%, var(--soft-blush) 100%);
    opacity: .8;
  }
  .front__tab {
    position: absolute; right: 0; top: 0; width: 54px; height: 12px;
    background: var(--brand-orange); border-bottom-left-radius: 6px;
  }
  .identity {
    position: absolute; right: 26px; top: 40px; text-align: right;
  }
  .identity__name {
    font-family: "Roboto Condensed", sans-serif; font-weight: 500;
    font-size: 20px; letter-spacing: .5px; color: var(--deep-orange); text-transform: uppercase;
  }
  .identity__role {
    font-family: "Roboto Condensed", sans-serif; font-size: 14px; line-height: 1.25;
    color: var(--gold); text-transform: uppercase; letter-spacing: .4px;
  }
  .brand {
    position: absolute; left: 40px; top: 118px;
    display: flex; align-items: center; gap: 10px;
  }
  .brand__dot {
    width: 22px; height: 22px; border-radius: 50%; background: var(--brand-orange);
  }
  .brand__name {
    font-family: "Roboto", sans-serif; font-weight: 500; font-size: 28px;
    color: var(--brand-orange); letter-spacing: 1px;
  }
  .contacts {
    position: absolute; left: 40px; bottom: 26px; list-style: none;
    font-size: 12.5px; color: var(--ink); line-height: 1.5;
  }
  .contacts li { display: flex; align-items: center; gap: 8px; }
  .contacts svg { width: 11px; height: 11px; flex: none; }

  /* back */
  .back__tagline {
    position: absolute; left: 28px; top: 22px;
    font-size: 13px; color: var(--white); letter-spacing: .3px;
  }
  .back__brand {
    position: absolute; left: 0; right: 0; top: 128px;
    text-align: center;
    font-family: "Roboto", sans-serif; font-weight: 500; font-size: 34px;
    color: var(--white); letter-spacing: 2px;
  }
  .social {
    position: absolute; right: 24px; bottom: 22px; display: flex; gap: 8px; list-style: none;
  }
  .social li {
    width: 18px; height: 18px; border-radius: 50%; border: 1.5px solid var(--white);
  }
  .social li:first-child { background: var(--white); }
</style>
</head>
<body>
  <section class="card card--front" aria-label="Business card front">
    <div class="front__wash" role="img" aria-label="Soft peach background wash"></div>
    <div class="front__tab"></div>

    <div class="identity">
      <p class="identity__name">Mathilde T.</p>
      <p class="identity__role">Communication Coach<br>Chief Lion</p>
    </div>

    <div class="brand">
      <span class="brand__dot"></span>
      <p class="brand__name">TIDEBLOOM</p>
    </div>

    <ul class="contacts">
      <li><svg viewBox="0 0 12 12"><path d="M3 1 L5 3.5 L4 5 Q5 7 7 8 L8.5 7 L11 9 L9.5 11 Q4 10.5 1 3 Z" fill="var(--brand-orange)"/></svg>514-555-0147</li>
      <li><svg viewBox="0 0 12 12"><rect x="3" y="1" width="6" height="10" rx="1" fill="none" stroke="var(--brand-orange)" stroke-width="1.4"/></svg>514-555-0183</li>
      <li><svg viewBox="0 0 12 12"><rect x="1" y="2.5" width="10" height="7" rx="1" fill="var(--brand-orange)"/><path d="M1.5 3 L6 6.5 L10.5 3" fill="none" stroke="#fff" stroke-width="1"/></svg>mathilde@tidebloom.com</li>
      <li><svg viewBox="0 0 12 12"><circle cx="6" cy="6" r="5" fill="var(--brand-orange)"/></svg>www.tidebloom.com</li>
    </ul>
  </section>

  <section class="card card--back" aria-label="Business card back">
    <p class="back__tagline">Creating Videos as unique as you</p>
    <p class="back__brand">TIDEBLOOM</p>
    <ul class="social" aria-label="Social profiles">
      <li></li><li></li><li></li>
    </ul>
  </section>
</body>
</html>
```